Broschüre für Personaldienstleister
Zielgruppe
Wir sind ein Personaldienstleister und vermitteln ausländisches medizinisches Fachpersonal an deutsche Einrichtungen. Unsere Zielgruppe sind Krankenhäuser, Pflegeheime, Ärztehäuser, Praxen, Labore und weitere medizinische Institutionen.
Aufgabenstellung
Wir haben eine Infobroschüre sowie eine PowerPoint Präsentation bereits mit einem groben Design erstellt. Texte und Beispielbilder (Stockmaterial) sind ebenfalls vorhanden, gerne wünschen wir uns auch Eigeninitiative bei der Wahl der Bilder passend zum neuen Design.
Wir wünschen uns ein Redesign mit einem kreativen, einzigartigen Design. Zudem ist uns wichtig, dass unsere Infografiken qualitativ und hochwertig gestaltet werden.
Dieses Projekt ist mit zukünftigen Folgeprojekten verbunden, da wir weitere Präsentationen und Broschüren für andere Zielgruppen benötigen.

```html
<!DOCTYPE html>
<html lang="de">
<head>
<meta charset="utf-8">
<title>Corvana HR – Broschüre</title>
<link rel="stylesheet" href="https://fonts.googleapis.com/css2?family=Poppins:wght@500;600;700&family=Open+Sans:wght@400;600;700&display=swap">
<style>
  :root {
    --bg: #e4e4e4;
    --paper: #f4f4f3;
    --green: #2b7a5f;
    --green-mid: #4f9c82;
    --green-light: #acd0c2;
    --teal-dark: #103c3d;
    --slate: #3d5a5c;
    --text: #3c3c3c;
    --dark-page: #262626;
    --white: #ffffff;
  }
  * { margin: 0; padding: 0; box-sizing: border-box; }
  html, body { width: 1200px; height: 865px; overflow: hidden; background: var(--bg); }
  body { font-family: "Open Sans", Arial, sans-serif; color: var(--text); }

  .spread {
    position: absolute; left: 48px; top: 42px;
    width: 1104px; height: 780px; display: flex;
    box-shadow: 0 14px 40px rgba(0,0,0,.25);
  }
  .page { position: relative; width: 552px; height: 780px; overflow: hidden; }

  /* Left page */
  .page-intro { background: linear-gradient(90deg, var(--paper) 0%, #ececeb 100%); }
  .claims { position: absolute; left: 0; top: 40px; }
  .claim {
    display: block; font-family: "Poppins", Arial, sans-serif; font-weight: 700;
    font-size: 24px; line-height: 32px; padding: 0 14px 0 22px; width: max-content;
  }
  .claim-modern { background: var(--green); color: var(--white); }
  .claim-kompetent { background: var(--green-light); color: #e6f1ec; margin-left: 4px; }
  .claim-interkulturell { background: var(--teal-dark); color: var(--white); margin-left: 8px; }

  .intro-title {
    position: absolute; left: 22px; top: 144px;
    font-family: "Poppins", Arial, sans-serif; font-weight: 700;
    font-size: 21px; color: var(--green);
  }
  .intro-copy {
    position: absolute; left: 22px; top: 178px; width: 232px;
    font-size: 9px; line-height: 1.34; text-align: justify;
  }
  .intro-copy p { margin-bottom: 9px; }
  .intro-copy strong { color: var(--teal-dark); }

  .photo-team {
    position: absolute; left: 270px; top: 48px; width: 262px; height: 318px;
    background: linear-gradient(160deg, #d7dee0 0%, #a9afb2 45%, #4d545a 100%);
  }

  .philosophy-title {
    position: absolute; left: 160px; top: 492px;
    font-family: "Poppins", Arial, sans-serif; font-weight: 700;
    font-size: 28px; color: var(--teal-dark); line-height: 1.1;
  }
  .philosophy-sub {
    display: block; font-size: 14px; font-weight: 600; color: var(--green);
    margin-left: 22px;
  }

  .ring { position: absolute; left: 0; top: 0; z-index: 2; }
  .value {
    position: absolute; color: var(--white); font-size: 6.8px; line-height: 1.35;
  }
  .value h3 { font-size: 7.6px; font-weight: 700; margin-bottom: 1px; }
  .value-left {
    width: 180px; padding: 8px 28px 8px 12px;
    clip-path: polygon(0 0, 86% 0, 100% 50%, 86% 100%, 0 100%); border-radius: 12px 0 0 12px;
  }
  .value-right {
    width: 190px; padding: 8px 12px 8px 34px;
    clip-path: polygon(14% 0, 100% 0, 100% 100%, 14% 100%, 0 50%); border-radius: 0 12px 12px 0;
  }
  .value-respekt { left: 16px; top: 598px; background: var(--teal-dark); }
  .value-vertrauen { left: 16px; top: 688px; background: var(--green-mid); }
  .value-fair { left: 346px; top: 552px; background: var(--green-mid); }
  .value-besser { left: 346px; top: 642px; background: var(--slate); }

  /* Right page */
  .page-vision { background: var(--dark-page); }
  .photo-steps {
    position: absolute; inset: 0;
    background: radial-gradient(ellipse at 40% 40%, #3a3a3a 0%, #262626 55%, #1a1a1a 100%);
  }
  .brand {
    position: absolute; right: 34px; top: 36px; display: flex; align-items: center; gap: 8px;
    font-family: "Poppins", Arial, sans-serif; font-weight: 700; font-size: 22px; color: var(--white);
  }
  .brand-mark { width: 14px; height: 14px; background: var(--white); }
  .vision-copy {
    position: absolute; left: 318px; top: 550px; width: 214px;
    color: var(--white); font-size: 9.6px; line-height: 1.32;
  }
  .vision-copy h2 { font-size: 11px; font-weight: 700; }
  .vision-copy p { margin-bottom: 16px; }
</style>
</head>
<body>
<main class="spread">
  <section class="page page-intro">
    <div class="claims">
      <span class="claim claim-modern">Modern.</span>
      <span class="claim claim-kompetent">Kompetent.</span>
      <span class="claim claim-interkulturell">Interkulturell.</span>
    </div>

    <h1 class="intro-title">Wir stellen uns vor!</h1>
    <div class="intro-copy">
      <p><strong>Corvana HR</strong> ist ein deutscher Personaldienstleister mit türkischen Wurzeln. Als Tochterunternehmen der Corvana Gruppe hat sich Corvana HR zum Ziel gesetzt, menschliche Gesundheitsdienstleistungen zu globalisieren. Dabei rekrutieren wir vor allem qualifizierte Fachkräfte aus der Türkei, um sie in den deutschen Arbeitsmarkt zu integrieren. Auf diese Weise wollen wir dem großen Fachkräftemangel in der Pflege- und Gesundheitsbranche entgegenwirken und gleichzeitig ausländischen Pflegekräften eine neue berufliche Perspektive bieten.</p>
      <p>Unser Name setzt sich aus den lateinischen Begriffen Servitium (=Dienstleistung) und Humanitas (=Menschlichkeit) zusammen und beschreibt damit den Kern unseres Handelns: den Dienst am Menschen.</p>
      <p>Dabei geht es uns um mehr, als nur um die Zusammenführung von medizinischen Einrichtungen und qualifiziertem Fachpersonal. Wir glauben an den Grundsatz, dass persönliche Dienstleistungen sowohl in einem nachhaltigen und fairen Prozess als auch im Einklang mit universellen menschlichen Werten globalisiert werden können.</p>
    </div>

    <div class="photo-team" role="img" aria-label="Foto: Geschäftsfrau und Geschäftsmann besprechen ein Dokument im Büro"></div>

    <h2 class="philosophy-title">Unsere Philosophie
      <span class="philosophy-sub">Dienstleistung die verbindet</span>
    </h2>

    <div class="value value-left value-respekt">
      <h3>Respektvoll</h3>
      Wir legen Wert auf Pluralismus und dank unserer kultur- und religionssensiblen Struktur, steht der respektvolle Umgang mit unseren Kund:innen und Partner:innen immer an erster Stelle.
    </div>
    <div class="value value-left value-vertrauen">
      <h3>Vertrauensvoll</h3>
      Wir bauen ehrliche und verlässliche Beziehungen auf, die auf dem Prinzip der Verantwortlichkeit beruhen. Wir wissen, dass Vertrauen an erster Stelle stehen muss und wir handeln entsprechend.
    </div>
    <div class="value value-right value-fair">
      <h3>Fair</h3>
      Fairness motiviert und bindet Partner:innen, Führungskräfte und Mitarbeiter:innen. Deshalb haben wir Fairness als Verhaltensmaxime in all unseren Unternehmen fest verankert.
    </div>
    <div class="value value-right value-besser">
      <h3>Zum Besseren</h3>
      Um die Zusammenarbeit mit unseren Kund:innen und Mitarbeiter:innen nachhaltig zu stärken und gleichzeitig der Gesellschaft etwas zurückzugeben, streben wir danach, besser als gut zu sein. Deshalb halten wir nicht an Bewährtem fest, sondern streben ständig danach Besseres zu leisten.
    </div>

    <svg class="ring" width="552" height="780" viewBox="0 0 552 780" aria-hidden="true">
      <circle cx="276" cy="658" r="84" fill="none" stroke="#d5e6df" stroke-width="8"/>
      <circle cx="276" cy="658" r="40" fill="var(--green)"/>
      <circle cx="276" cy="658" r="30" fill="var(--teal-dark)"/>
      <g fill="#ffffff" stroke="#dfe9e5" stroke-width="2">
        <circle cx="214" cy="634" r="18"/>
        <circle cx="214" cy="726" r="18"/>
        <circle cx="330" cy="590" r="18"/>
        <circle cx="330" cy="694" r="18"/>
      </g>
      <g fill="none" stroke="var(--teal-dark)" stroke-width="1.8" stroke-linecap="round" stroke-linejoin="round">
        <path d="M204 636 l6 -5 l8 6 l6 -5 M206 638 l8 5 l6 -3"/>
        <path d="M205 726 a9 9 0 0 1 18 0 z M214 726 v8 a2 2 0 0 0 4 0"/>
        <path d="M322 596 v-4 M330 596 v-4 M338 596 v-4 M326 584 a3 3 0 1 0 0.1 0 M334 584 a3 3 0 1 0 0.1 0"/>
        <path d="M322 702 h4 v-10 h-4 z M326 692 l5 -7 l2 1 l-1 6 h6 l-2 10 h-10"/>
      </g>
    </svg>
  </section>

  <section class="page page-vision">
    <div class="photo-steps" role="img" aria-label="Foto: Mann im Anzug steigt auf mit Kreide gezeichnete Treppenstufen"></div>
    <div class="brand"><span>Corvana HR</span><span class="brand-mark"></span></div>
    <div class="vision-copy">
      <h2>Unsere Vision</h2>
      <p>Wir handeln mit der festen Überzeugung, dass wir mit unserer innovativen und dynamischen Organisation das Gesundheitswesen mit qualitativ hochwertigen HR-Lösungen nachhaltig globalisieren können.</p>
      <h2>Unser Ziel</h2>
      <p>Unser Anspruch ist, der führende internationale Personaldienstleister im Gesundheitswesen für den deutsch-türkischen Markt zu sein, der sich für moderne und zuverlässige sowie kundenorientierte Dienstleistungen auszeichnet.</p>
    </div>
  </section>
</main>
</body>
</html>
```